Simple and Clean business card design

We would like the design to be simple clean and to incorporate our colors.

We are open to your design and talent, we have the dots in our logo as we think of it as data points and we connect data points for people.

We are open to see the great creative and clean design you bring to the table

Contact Information for Business Card

please include: name, position, email, phone and website

Font styles to use
Sans Serif

Requirements
Must have
• my colors incorporated, simplicity
Nice to have
• lots of white space, simplicity
Should not have
• complexicity/ complex art

```html
<!DOCTYPE html>
<html lang="en">
<head>
<meta charset="utf-8">
<title>Nodara business card</title>
<link href="https://fonts.googleapis.com/css2?family=Open+Sans:wght@400;500;600&family=Rubik:wght@500;600&display=swap" rel="stylesheet">
<style>
  :root {
    --brand-blue: #4285f4;
    --ink: #222222;
    --black: #000000;
    --paper: #ffffff;
    --band-dark: #222222;
    --card-edge: #333333;
  }
  * { box-sizing: border-box; margin: 0; padding: 0; }
  html, body {
    width: 1200px; height: 1200px; overflow: hidden;
    background: var(--paper);
  }
  .canvas { position: relative; width: 1200px; height: 1200px; }
  .card {
    position: absolute; left: 216px; width: 775px; height: 430px;
    border: 1px solid var(--card-edge); overflow: hidden;
  }
  .card--front { top: 144px; background: var(--brand-blue); }
  .card--back { top: 635px; background: var(--paper); }

  .wordmark {
    position: absolute; font-family: "Open Sans", sans-serif; font-weight: 600;
    line-height: 1; white-space: nowrap;
  }
  .card--front .wordmark {
    left: 0; right: 0; top: 152px; text-align: center;
    font-size: 112px; color: var(--paper);
  }

  .front-web {
    position: absolute; top: 346px; left: 0; right: 0;
    display: flex; justify-content: center; align-items: center; gap: 34px;
    font-family: "Open Sans", sans-serif; font-size: 19px; color: var(--paper);
  }
  .front-web__rule { width: 104px; height: 2px; background: var(--paper); }

  .card--back .wordmark {
    right: 43px; top: 31px; font-size: 88px; color: var(--black);
  }

  .person { position: absolute; left: 31px; top: 161px; }
  .person__name {
    font-family: "Rubik", sans-serif; font-weight: 600; font-size: 34px;
    color: var(--brand-blue); letter-spacing: 1px; line-height: 1;
  }
  .person__role {
    margin-top: 2px; font-family: "Rubik", sans-serif; font-weight: 500;
    font-size: 15px; letter-spacing: 2.5px; color: var(--ink); line-height: 1.2;
  }
  .divider {
    position: absolute; left: 32px; top: 216px; width: 674px; height: 1px;
    background: linear-gradient(to right, var(--brand-blue), rgba(66,133,244,0.05));
  }
  .contacts { position: absolute; left: 32px; top: 237px; list-style: none; }
  .contact { display: flex; align-items: center; height: 44px; margin-bottom: 2px; }
  .contact__icon {
    width: 44px; height: 43px; border: 3px solid var(--ink); border-radius: 7px;
    padding: 2px; flex: none;
  }
  .contact__icon-inner {
    width: 100%; height: 100%; background: var(--brand-blue); border-radius: 4px;
    display: flex; align-items: center; justify-content: center;
  }
  .contact__text {
    margin-left: 16px; font-family: "Open Sans", sans-serif; font-size: 23px;
    font-weight: 500; color: var(--ink);
  }
  .back-web {
    position: absolute; right: 43px; top: 357px; line-height: 1.2;
    font-family: "Open Sans", sans-serif; font-size: 20px; font-weight: 500; color: var(--ink);
  }
  .footer-band { position: absolute; left: 0; top: 391px; width: 775px; height: 22px; }
</style>
</head>
<body>
<div class="canvas">
  <section class="card card--front">
    <div class="wordmark">Nodara</div>
    <div class="front-web">
      <span class="front-web__rule"></span>
      <span>www.nodara.one</span>
      <span class="front-web__rule"></span>
    </div>
  </section>

  <section class="card card--back">
    <div class="wordmark">Nodara</div>
    <div class="person">
      <h1 class="person__name">DANIEL MOSS</h1>
      <p class="person__role">FOUNDER</p>
    </div>
    <div class="divider"></div>
    <ul class="contacts">
      <li class="contact">
        <span class="contact__icon"><span class="contact__icon-inner">
          <svg width="14" height="24" viewBox="0 0 14 24"><rect x="1" y="1" width="12" height="22" rx="2" fill="none" stroke="#fff" stroke-width="1.5"/><circle cx="7" cy="20" r="1" fill="#fff"/></svg>
        </span></span>
        <span class="contact__text">555-014-2290</span>
      </li>
      <li class="contact">
        <span class="contact__icon"><span class="contact__icon-inner">
          <svg width="24" height="16" viewBox="0 0 24 16"><rect x="1" y="1" width="22" height="14" fill="none" stroke="#fff" stroke-width="1.5"/><path d="M1 1 L12 10 L23 1 M1 15 L9 8 M23 15 L15 8" fill="none" stroke="#fff" stroke-width="1.2"/></svg>
        </span></span>
        <span class="contact__text">daniel.moss@nodara.one</span>
      </li>
      <li class="contact">
        <span class="contact__icon"><span class="contact__icon-inner">
          <svg width="22" height="22" viewBox="0 0 22 22" fill="none" stroke="#fff" stroke-width="1.1"><circle cx="11" cy="11" r="10"/><ellipse cx="11" cy="11" rx="4.5" ry="10"/><path d="M1 11 H21 M3 5.5 H19 M3 16.5 H19 M11 1 V21"/></svg>
        </span></span>
        <span class="contact__text">www.nodara.one</span>
      </li>
    </ul>
    <div class="back-web">www.nodara.one</div>
    <svg class="footer-band" viewBox="0 0 775 22" preserveAspectRatio="none">
      <polygon points="0,0 558,0 548,22 0,22" fill="var(--brand-blue)"/>
      <polygon points="565,0 775,0 775,22 555,22" fill="var(--band-dark)"/>
    </svg>
  </section>
</div>
</body>
</html>
```